Unique Business Card Design

Unique Business Card design for our orthotic and prosthetic company. Our logo is on our website, color is light blue. Unique shape (artificial leg shaped, vertical, etc..) preferred. Logo, business name, individual name and basic demographics needed.

Industry/Entity Type

Business

Contact Information for Business Card

Logo, Industry, Phone # Logo, "Prosthetic & Orthotic Services" Place to add individual name and contact info

Colors
cee9f5

Requirements
Must have
• The icon must be there, placement of "Prosthetic & Orthotic Services" can be moved
Nice to have
• Like the mix of light blue, and a little darker blue. One design included the icons from my website which was a nice touch

```html
<!DOCTYPE html>
<html lang="en">
<head>
<meta charset="utf-8">
<title>Stridewell Inc. – Business Card</title>
<link rel="stylesheet" href="https://fonts.googleapis.com/css2?family=Open+Sans:wght@400;600;700&family=Cormorant+Garamond:ital,wght@1,500&display=swap">
<style>
  :root {
    --brand-blue: #1e62b6;
    --brand-blue-deep: #174f98;
    --brand-light: #cee9f5;
    --card-white: #ffffff;
    --text-grey: #555b63;
    --rule-grey: #c9ccd1;
    --stripe-grey: #b9bcc1;
    --backdrop: #3a3a3a;
  }
  * { margin: 0; padding: 0; box-sizing: border-box; }
  html, body { width: 1200px; height: 950px; overflow: hidden; }
  body {
    background: radial-gradient(circle at 50% 45%, #4a4a4a 0%, var(--backdrop) 55%, #222 100%);
    font-family: "Open Sans", Arial, sans-serif;
    position: relative;
  }
  .card {
    position: absolute;
    width: 600px;
    height: 345px;
    border-radius: 18px;
    overflow: hidden;
    box-shadow: 0 14px 30px rgba(0,0,0,.45);
  }
  /* Front */
  .card-front {
    left: 80px; top: 90px;
    background: linear-gradient(160deg, #2a72c8 0%, var(--brand-blue) 55%, var(--brand-blue-deep) 100%);
    color: var(--card-white);
  }
  .brand-mark { position: absolute; border-radius: 50%; }
  .card-front .brand-mark { left: 70px; top: 120px; width: 96px; height: 96px; background: var(--card-white); }
  .brand-name { position: absolute; font-weight: 700; letter-spacing: .5px; white-space: nowrap; }
  .card-front .brand-name { left: 188px; top: 112px; font-size: 38px; }
  .brand-rule { position: absolute; height: 3px; }
  .card-front .brand-rule { left: 188px; top: 164px; width: 340px; background: var(--card-white); }
  .tagline { position: absolute; font-family: "Cormorant Garamond", Georgia, serif; font-style: italic; font-weight: 500; white-space: nowrap; }
  .card-front .tagline { left: 196px; top: 170px; font-size: 25px; }
  .front-divider { position: absolute; left: 200px; top: 245px; width: 360px; height: 1px; background: rgba(255,255,255,.55); }
  .front-web { position: absolute; left: 0; width: 100%; top: 262px; text-align: center; font-size: 15px; letter-spacing: .3px; }
  .front-base { position: absolute; left: 60px; top: 300px; width: 480px; height: 1px; background: rgba(255,255,255,.55); }

  /* Back */
  .card-back { left: 520px; top: 510px; background: var(--card-white); color: var(--text-grey); }
  .card-back .brand-mark { left: 196px; top: 72px; width: 66px; height: 66px; background: var(--brand-blue); }
  .card-back .brand-name { left: 275px; top: 56px; font-size: 27px; color: var(--brand-blue); }
  .card-back .brand-rule { left: 275px; top: 93px; width: 245px; height: 2px; background: var(--brand-blue); }
  .card-back .tagline { left: 282px; top: 95px; font-size: 18px; color: var(--brand-blue); }
  .back-divider { position: absolute; left: 200px; top: 152px; width: 375px; height: 1px; background: var(--rule-grey); }
  .address { position: absolute; right: 25px; top: 164px; text-align: right; font-size: 14px; line-height: 20px; font-style: normal; }
  .holder { position: absolute; left: 34px; top: 178px; font-size: 22px; font-weight: 700; color: var(--brand-blue); white-space: nowrap; }
  .holder small { font-size: 13px; font-weight: 600; }
  .contacts { position: absolute; left: 34px; top: 214px; list-style: none; font-size: 14px; line-height: 21px; }
  .contacts li { display: flex; align-items: center; gap: 8px; }
  .contacts svg { width: 14px; height: 14px; fill: var(--brand-blue); flex: none; }
  .wave { position: absolute; left: 0; top: 0; width: 600px; height: 345px; }
</style>
</head>
<body>
  <section class="card card-front" aria-label="Card front">
    <div class="brand-mark"></div>
    <div class="brand-name">STRIDEWELL INC.</div>
    <div class="brand-rule"></div>
    <div class="tagline">Prosthetic &amp; Orthotic Services</div>
    <div class="front-divider"></div>
    <div class="front-web">www.stridewellinc.com</div>
    <div class="front-base"></div>
  </section>

  <section class="card card-back" aria-label="Card back">
    <svg class="wave" viewBox="0 0 600 345" aria-hidden="true">
      <path d="M0 345 L0 310 C200 335 430 320 600 245 L600 345 Z" fill="var(--stripe-grey)"/>
      <path d="M0 345 L0 325 C200 345 440 332 600 262 L600 345 Z" fill="var(--brand-blue)"/>
    </svg>
    <div class="brand-mark"></div>
    <div class="brand-name">STRIDEWELL INC.</div>
    <div class="brand-rule"></div>
    <div class="tagline">Prosthetic &amp; Orthotic Services</div>
    <div class="back-divider"></div>
    <address class="address">
      820 Harbor Ave.<br>Fairview, NY 10090<br>www.stridewellinc.com
    </address>
    <div class="holder">Miriam Kessler, <small>CO LPO</small></div>
    <ul class="contacts">
      <li><svg viewBox="0 0 16 16"><path d="M3 1h3l1.5 4-2 1.3a9 9 0 0 0 4.2 4.2L11 8.5l4 1.5v3a2 2 0 0 1-2 2A12 12 0 0 1 1 3a2 2 0 0 1 2-2z"/></svg>555.014.2200</li>
      <li><svg viewBox="0 0 16 16"><path d="M4 0h8a1 1 0 0 1 1 1v14a1 1 0 0 1-1 1H4a1 1 0 0 1-1-1V1a1 1 0 0 1 1-1zm1 2v10h6V2zm3 11a1 1 0 1 0 0 2 1 1 0 0 0 0-2z"/></svg>555.014.2291</li>
      <li><svg viewBox="0 0 16 16"><path d="M4 1h8v4H4zM1 6h14v7h-3v2H4v-2H1zm4 5v3h6v-3z"/></svg>555-0187316</li>
      <li><svg viewBox="0 0 16 16"><path d="M1 3h14v10H1zm1.5 1.5L8 9l5.5-4.5z"/></svg>mkessler@stridewellinc.com</li>
    </ul>
  </section>
</body>
</html>
```